Baby Boutique Needs a Business Card Design

We need a modern double sided business card design using the attached logo for Little Wren Nook.

Little Wren Nook is a baby boutique which sells only handmade clothing and accessories for both boys and girls. Our store will live exclusively online.

We would like to only use the colors that have been used in the logo.

Target Market(s)

Potential wholesale clients, Small business owners

Industry/Entity Type

Retail

Contact Information for Business Card

Name Gideon R. Falkner (Owner)
Email sales@littlewrennook.example
Main Phone 555-203-7719
Cell phone 555-203-7746
Website www.LittleWrenNook.example

Font styles to use
Sans Serif

Colors

Designer to choose colors to be used in the design.

Requirements
Must have
• -Would like to have icons that indentify the contact information.
• -Include our website
• -Include our tagline in a small area near the bottom. "Handmade Baby Creations"
• -Would like to include Facebook and Instagram Icons
• -
Nice to have
• Would like to have a simple back side with the logo.
• Something along the lines of the meadowfield lending card attached.

```html
<!DOCTYPE html>
<html lang="en">
<head>
<meta charset="utf-8">
<title>Little Wren Nook – Business Card</title>
<link rel="stylesheet" href="https://fonts.googleapis.com/css2?family=Poppins:wght@300;400;600&display=swap">
<style>
  :root {
    --canvas: #dcdcdc;
    --card: #131313;
    --teal: #74cdbf;
    --coral: #e05e5c;
    --white: #f4f4f4;
    --muted: #cfcfcf;
  }
  * { box-sizing: border-box; margin: 0; padding: 0; }
  html, body { width: 1200px; height: 856px; overflow: hidden; }
  body {
    background: var(--canvas);
    font-family: "Poppins", sans-serif;
    position: relative;
  }
  .card {
    position: absolute;
    width: 660px;
    height: 377px;
    background: var(--card);
    box-shadow: 0 14px 30px rgba(0,0,0,0.22);
    overflow: hidden;
  }
  .card--back { left: 110px; top: 36px; }
  .card--front { left: 430px; top: 443px; }

  .wordmark {
    color: var(--teal);
    font-weight: 600;
    line-height: 1.02;
    letter-spacing: -0.5px;
  }
  .card--back .wordmark {
    position: absolute;
    left: 0; right: 0; top: 50%;
    transform: translateY(-50%);
    text-align: center;
    font-size: 58px;
  }
  .card--front .wordmark {
    position: absolute;
    right: 46px; top: 56px;
    width: 230px;
    text-align: center;
    font-size: 40px;
  }

  .owner {
    position: absolute;
    left: 40px; top: 58px;
  }
  .owner__name {
    color: var(--coral);
    font-weight: 300;
    font-size: 26px;
    letter-spacing: 0.5px;
  }
  .owner__rule {
    display: block;
    width: 330px;
    height: 1.5px;
    background: var(--coral);
    margin-top: 2px;
  }
  .owner__role {
    color: var(--white);
    font-weight: 300;
    font-size: 13px;
    letter-spacing: 1px;
    margin-left: 18px;
  }

  .contacts {
    position: absolute;
    left: 46px; top: 160px;
    list-style: none;
  }
  .contacts__item {
    display: flex;
    align-items: center;
    gap: 12px;
    height: 31px;
    color: var(--white);
    font-size: 15px;
    font-weight: 300;
    letter-spacing: 0.3px;
  }
  .contacts__icon { width: 22px; height: 22px; flex: none; }

  .social {
    position: absolute;
    left: 46px; top: 296px;
    display: flex;
    gap: 8px;
  }
  .social__dot {
    width: 22px; height: 22px;
    border: 1.5px solid var(--teal);
    border-radius: 50%;
  }

  .tagline-band {
    position: absolute;
    left: 226px; right: 0; bottom: 0;
    height: 64px;
    background: var(--coral);
    display: flex;
    align-items: center;
    justify-content: center;
    color: var(--white);
    font-size: 19px;
    font-weight: 300;
    letter-spacing: 3px;
  }
</style>
</head>
<body>

  <section class="card card--back" aria-label="Business card, back side">
    <p class="wordmark">Little Wren<br>Nook</p>
  </section>

  <section class="card card--front" aria-label="Business card, front side">
    <p class="wordmark">Little Wren<br>Nook</p>

    <div class="owner">
      <p class="owner__name">Gideon R. Falkner</p>
      <span class="owner__rule"></span>
      <p class="owner__role">owner</p>
    </div>

    <ul class="contacts">
      <li class="contacts__item">
        <svg class="contacts__icon" viewBox="0 0 22 22" aria-hidden="true">
          <circle cx="11" cy="11" r="10" fill="none" stroke="var(--coral)" stroke-width="1.5"/>
          <path d="M7.5 6.5 L9.5 6.5 L10.3 9 L9 10 Q10 12.3 12 13 L13 11.7 L15.5 12.5 L15.5 14.5 Q11 15 8.5 12 Q6.8 9.5 7.5 6.5 Z" fill="var(--coral)"/>
        </svg>
        555-203-7719
      </li>
      <li class="contacts__item">
        <svg class="contacts__icon" viewBox="0 0 22 22" aria-hidden="true">
          <circle cx="11" cy="11" r="10" fill="none" stroke="var(--coral)" stroke-width="1.5"/>
          <rect x="8" y="5.5" width="6" height="11" rx="1.2" fill="none" stroke="var(--coral)" stroke-width="1.4"/>
          <circle cx="11" cy="14.3" r="0.8" fill="var(--coral)"/>
        </svg>
        555-203-7746
      </li>
      <li class="contacts__item">
        <svg class="contacts__icon" viewBox="0 0 22 22" aria-hidden="true">
          <circle cx="11" cy="11" r="10" fill="none" stroke="var(--coral)" stroke-width="1.5"/>
          <rect x="6" y="7.5" width="10" height="7" fill="var(--coral)"/>
          <path d="M6 7.5 L11 11.5 L16 7.5" fill="none" stroke="var(--card)" stroke-width="1.2"/>
        </svg>
        sales@littlewrennook.example
      </li>
      <li class="contacts__item">
        <svg class="contacts__icon" viewBox="0 0 22 22" aria-hidden="true">
          <circle cx="11" cy="11" r="10" fill="none" stroke="var(--coral)" stroke-width="1.5"/>
          <circle cx="11" cy="11" r="5.5" fill="none" stroke="var(--coral)" stroke-width="1.3"/>
          <ellipse cx="11" cy="11" rx="2.3" ry="5.5" fill="none" stroke="var(--coral)" stroke-width="1.1"/>
          <line x1="5.5" y1="11" x2="16.5" y2="11" stroke="var(--coral)" stroke-width="1.1"/>
        </svg>
        www.LittleWrenNook.example
      </li>
    </ul>

    <div class="social" aria-label="Social profiles">
      <span class="social__dot"></span>
      <span class="social__dot"></span>
    </div>

    <div class="tagline-band">Handmade Baby Creations</div>
  </section>

</body>
</html>
```